Modern Verdell Tree Care Website

I need a website for a full service Tree Care company. The company provides tree pruning, tree removal, tree preservation, emergency services, stump grinding, and emergency tree services.

Target Market(s)

Customers that need tree services

Industry/Entity Type

Landscaping, Tree Services

Coding

Coded - Design and coding required

Number of Pages Required

5+ page

Font styles to use
Sans Serif

Requirements
Must have
• Good clean design that showcases the services the company provides.
Nice to have
• Services page; contact form, blog, home page, about page

```html
<!DOCTYPE html>
<html lang="en">
<head>
<meta charset="utf-8">
<title>Verdell Tree Care</title>
<link href="https://fonts.googleapis.com/css2?family=Fira+Sans:wght@400;500;600;700&family=Open+Sans:wght@400;600;700&family=Libre+Baskerville:wght@400;700&display=swap" rel="stylesheet">
<style>
:root{
  --navy:#14215c;
  --navy-dark:#0f1b4d;
  --footer:#1c3550;
  --green:#7ebd3e;
  --green-dark:#5f9a2a;
  --orange:#f39a2c;
  --ink:#3b3f55;
  --muted:#8a8fa3;
  --pale:#eef3fb;
  --field:#eceff7;
  --white:#ffffff;
  --blue:#1f6fd8;
}
*{margin:0;padding:0;box-sizing:border-box}
html,body{width:1200px;height:4097px;overflow:hidden}
body{position:relative;font-family:"Open Sans",sans-serif;color:var(--ink);background:var(--white)}
.abs{position:absolute}
.heading{font-family:"Fira Sans",sans-serif;font-weight:600;color:var(--navy)}
.eyebrow{font-size:13px;letter-spacing:.3px;color:var(--green);text-transform:uppercase;padding-bottom:4px;border-bottom:2px solid var(--green)}
.btn{display:flex;align-items:center;justify-content:center;background:var(--green);color:var(--white);font-family:"Fira Sans",sans-serif;font-weight:600}

/* header */
.header{left:0;top:0;width:1200px;height:103px;background:var(--white);z-index:3}
.brand{left:132px;top:24px;display:flex;align-items:center;gap:12px}
.brand-mark{width:44px;height:44px;background:var(--green)}
.brand-name{font-family:"Fira Sans",sans-serif;font-weight:700;font-size:22px;color:var(--green-dark);line-height:1.1;letter-spacing:1px}
.topbar{left:390px;top:0;width:810px;height:32px;background:var(--navy-dark);display:flex;align-items:center;font-size:11px;color:var(--white);font-weight:600}
.topbar .phone{width:204px;display:flex;align-items:center;gap:8px;padding-left:54px}
.topbar .appoint{width:232px;height:32px;background:var(--green);display:flex;align-items:center;justify-content:center;gap:8px;font-weight:400}
.topbar .addr{display:flex;align-items:center;gap:8px;padding-left:30px;font-weight:400}
.nav{left:396px;top:59px;display:flex;gap:0;font-size:11.5px;font-weight:600;color:#333}
.nav span{display:inline-block}
.contact-btn{left:930px;top:52px;width:119px;height:31px;border:2px solid var(--orange);border-radius:4px;color:var(--orange);font-size:11px;display:flex;align-items:center;justify-content:center}

/* hero */
.hero{left:0;top:103px;width:1200px;height:730px}
.hero-text{left:130px;top:300px;color:var(--white)}
.hero-kicker{font-size:13px;display:flex;align-items:center;gap:14px}
.hero-kicker i{display:block;width:48px;height:1px;background:var(--white)}
.hero h1{margin-top:20px;font-family:"Fira Sans",sans-serif;font-weight:600;font-size:43px;line-height:57px;color:var(--white)}
.hero p{margin-top:14px;width:385px;font-size:13px;line-height:21px}
.hero .btn{margin-top:30px;width:193px;height:40px;font-size:12.5px}
.badge{width:62px;height:62px;border-radius:50%;background:var(--white);box-shadow:0 4px 14px rgba(0,0,0,.18);display:flex;align-items:center;justify-content:center}
.badge i{display:block;width:22px;height:22px;background:var(--green)}

/* about */
.about{left:0;top:915px;width:1200px;text-align:center}
.about .eyebrow{display:inline-block}
.about h2{font-size:42px;margin-top:14px}
.about p{width:870px;margin:22px auto 0;font-size:13.5px;line-height:21.5px;color:#5c6785}
.about .btn{width:155px;height:44px;margin:18px auto 0;font-size:16px;gap:12px}

/* why choose */
.why{left:0;top:1306px;width:1200px;height:537px;background:var(--pale)}
.why-head{left:135px;top:50px}
.why h2{font-size:42px;line-height:52px;margin-top:22px}
.feature{width:219px;height:98px;background:var(--white);border-radius:6px;box-shadow:0 2px 10px rgba(20,33,92,.06);padding:16px 0 0 18px;display:flex;gap:14px}
.feature svg{flex:none}
.feature h3{font-family:"Fira Sans",sans-serif;font-weight:600;font-size:16px;color:var(--navy)}
.feature p{font-size:12.5px;line-height:20px;color:var(--muted);margin-top:4px}
.worker{left:683px;top:1184px;width:413px;height:659px;background:linear-gradient(180deg,#e88a3a 0%,#b9a893 14%,#6f7a8a 40%,#4c5868 65%,#9d6a33 100%);border-radius:180px 180px 0 0;opacity:.9}

/* services */
.services{left:0;top:1843px;width:1200px;height:664px;background:radial-gradient(ellipse at 50% 40%,#3b3c3a 0%,#262725 60%,#1b1c1b 100%)}
.services-head{left:0;top:62px;width:1200px;text-align:center}
.services .eyebrow{display:inline-block;color:var(--white);border-color:var(--white)}
.services h2{color:var(--white);font-size:42px;margin-top:14px}
.svc{width:304px;height:342px}
.svc-img{position:absolute;left:0;top:0;width:304px;height:297px;border-radius:14px}
.svc-card{position:absolute;left:22px;top:265px;width:260px;height:77px;background:var(--white);border-radius:12px;padding:16px 0 0 24px;box-shadow:0 4px 14px rgba(0,0,0,.2)}
.svc-card span{font-size:13px;color:var(--blue)}
.svc-card b{display:block;margin-top:4px;font-family:"Fira Sans",sans-serif;font-size:15px;font-weight:600;color:#222}
.svc-icon{position:absolute;left:120px;top:100px;width:64px;height:64px;border-radius:50%;background:var(--orange);display:flex;align-items:center;justify-content:center}

/* testimonials */
.avatar{border-radius:50%;border:5px solid var(--white);box-shadow:0 4px 16px rgba(0,0,0,.16)}
.timeline{left:546px;top:2630px;width:2px;height:365px;background:linear-gradient(180deg,rgba(31,111,216,0),#c9d3e6 20%,#c9d3e6 80%,rgba(31,111,216,0))}
.dot{width:14px;height:14px;border-radius:50%;border:2px solid var(--blue);background:var(--white)}
.dot.on{background:var(--blue)}
.quote{left:645px;top:2640px;width:420px}
.quote h2{font-family:"Libre Baskerville",serif;font-weight:700;font-size:44px;color:var(--navy)}
.stars{margin-top:26px;color:var(--orange);font-size:20px;letter-spacing:1px}
.quote p{margin-top:10px;font-size:11.5px;line-height:22px;color:#444}
.author{display:flex;align-items:center;gap:16px;margin-top:38px}
.author .avatar{width:70px;height:70px;border-width:3px}
.author b{display:block;font-family:"Libre Baskerville",serif;font-weight:400;font-size:20px;color:#222}
.author span{font-size:11px;color:#333}

/* contact */
.contact{left:0;top:3072px;width:1200px;height:670px;background:linear-gradient(180deg,#f6f8f6 0%,#eef2ea 55%,#c9d7b3 78%,#b7c99a 100%)}
.touch{left:134px;top:3178px;width:420px}
.touch h2{font-family:"Fira Sans",sans-serif;font-weight:400;font-size:34px;color:var(--navy)}
.touch h2 b{font-weight:600}
.touch p{margin-top:14px;font-size:12.5px;line-height:23px;color:#5c6785}
.info{display:flex;gap:20px;margin-top:34px}
.info .ic{width:44px;height:44px;border-radius:50%;background:var(--green);display:flex;align-items:center;justify-content:center;flex:none}
.info h4{font-size:13px;font-weight:700;color:var(--navy);letter-spacing:.4px}
.info span{display:block;font-size:13px;line-height:24px;color:#4a5270;margin-top:4px}
.socials{display:flex;gap:10px;margin-top:30px;padding-left:2px}
.socials i{display:block;width:38px;height:38px;border-radius:50%;background:var(--blue)}
.form{left:596px;top:3165px;width:478px;height:390px;background:var(--white);border:2px solid #dfe3ea;border-radius:6px;padding:40px 30px 0 34px}
.form h3{font-family:"Fira Sans",sans-serif;font-weight:600;font-size:19px;color:var(--navy);letter-spacing:.6px}
.field{width:414px;height:42px;background:var(--field);margin-top:16px;padding:14px 0 0 24px;font-size:12px;color:#6a7090}
.field.first{margin-top:20px}
.field.tall{height:98px}
.form .btn{width:414px;height:48px;margin-top:16px;font-size:16px;letter-spacing:.6px}

/* footer */
.footer{left:0;top:3700px;width:1200px;height:397px}
.foot-brand{left:108px;top:3795px}
.foot-brand .brand-name{color:var(--white);font-size:32px}
.foot-brand p{margin-top:28px;width:260px;font-size:13px;line-height:21px;color:#9fb0c4}
.foot-social{left:98px;top:3964px;display:flex;gap:44px}
.foot-social i{display:block;width:12px;height:12px;border-radius:50%;background:var(--white)}
.foot-col h4{font-size:14px;font-weight:700;color:var(--white)}
.foot-col li{list-style:none;font-size:13px;color:#b8c4d2;line-height:26px}
.news input{display:block}
.news-field{width:224px;height:30px;border:1px solid #7c8ea6;border-radius:3px;margin-top:22px;font-size:10px;color:#8fa0b6;padding:9px 0 0 14px}
.news-btn{width:120px;height:36px;background:var(--white);border-radius:3px;margin-top:14px;display:flex;align-items:center;justify-content:center;font-family:"Fira Sans",sans-serif;font-weight:700;font-size:16px;color:var(--navy)}
</style>
</head>
<body>

<!-- Hero -->
<section class="hero abs">
  <svg width="1200" height="730" class="abs" style="left:0;top:0">
    <defs>
      <linearGradient id="heroShade" x1="0" x2="1" y1="0" y2="0">
        <stop offset="0" stop-color="#141815"/>
        <stop offset=".45" stop-color="#2e3a28"/>
        <stop offset=".75" stop-color="#536a3a"/>
        <stop offset="1" stop-color="#46523c"/>
      </linearGradient>
    </defs>
    <path d="M0 0H1200V635Q1110 720 600 720Q130 720 0 635Z" fill="url(#heroShade)" role="img" aria-label="Photo of an arborist in safety gear cutting a large tree trunk"/>
    <path d="M245 705Q600 760 965 703" fill="none" stroke="var(--green)" stroke-width="5"/>
  </svg>
  <div class="hero-text abs" style="left:130px;top:197px">
    <div class="hero-kicker">On the other hand <i></i></div>
    <h1>We Offer Sustainable<br>Tree Solutions</h1>
    <p>Lorem ipsum dolor sit amet, consectetur adipiscing elit, sed do eiusmod tempor incididunt ut labore et dolore magna aliqua. Ut enim ad minim veniam, quis nostru ipsum dolor sit amet, co</p>
    <div class="btn">Discover more</div>
  </div>
</section>
<div class="badge abs" style="left:575px;top:808px"><i></i></div>

<!-- Header -->
<header class="header abs">
  <div class="brand abs">
    <div class="brand-mark"></div>
    <div class="brand-name">VERDELL<br>TREE CARE</div>
  </div>
  <div class="topbar abs">
    <div class="phone">
      <svg width="13" height="13" viewBox="0 0 24 24"><path d="M6.6 10.8a15 15 0 0 0 6.6 6.6l2.2-2.2a1 1 0 0 1 1-.25 11.4 11.4 0 0 0 3.6.57 1 1 0 0 1 1 1V20a1 1 0 0 1-1 1A17 17 0 0 1 3 4a1 1 0 0 1 1-1h3.5a1 1 0 0 1 1 1c0 1.25.2 2.45.57 3.6a1 1 0 0 1-.25 1z" fill="none" stroke="#fff" stroke-width="1.6"/></svg>
      555 - 210 - 4482
    </div>
    <div class="appoint">
      <svg width="12" height="12" viewBox="0 0 24 24"><rect x="3" y="5" width="18" height="16" rx="2" fill="none" stroke="#fff" stroke-width="2"/><path d="M3 10h18M8 3v4M16 3v4" stroke="#fff" stroke-width="2"/></svg>
      REQUEST AN APPOINTMENT
    </div>
    <div class="addr">
      <svg width="11" height="13" viewBox="0 0 24 28"><path d="M12 26s9-9 9-15a9 9 0 0 0-18 0c0 6 9 15 9 15z" fill="none" stroke="#fff" stroke-width="2.2"/><circle cx="12" cy="11" r="3" fill="#fff"/></svg>
      88 Birchwood Lane, Oakridge
    </div>
  </div>
  <nav class="nav abs">
    <span style="width:74px">Home</span><span style="width:75px">About Us</span><span style="width:75px">Services</span><span style="width:76px">Projects</span><span>And more</span>
  </nav>
  <div class="contact-btn abs">CONTACT US</div>
</header>

<!-- Who we are -->
<section class="about abs">
  <div class="eyebrow">Who we are</div>
  <h2 class="heading">Your Tree Care Professionals</h2>
  <p>Lorem ipsum dolor sit amet, consectetur adipiscing elit, sed do eiusmod tempor incididunt ut labore et dolore magna aliqua. Ut enim ad minim veniam, quis laboris nisi ut aliquip ex ea commodo consequat. Lorem ipsum dolor sit am et, consectetur adipiscing elit, sed do eiusmod tempor incididunt ut labore et dolore magna aliqua. Ut enim ad minim veniam, quis nost rud exercitation ullamco laboris nisi ut aliquip ex ea commodo consequat. Duis aute irure dolor in reprehenderit in voluptate velit esse cillum dolore eu fugiat nulla pariatur. Excepteur sint occaecat cupidatat</p>
  <div class="btn">Contact us
    <svg width="18" height="14" viewBox="0 0 18 14"><path d="M1 7h15M10 1l6 6-6 6" fill="none" stroke="#fff" stroke-width="1.8"/></svg>
  </div>
</section>

<!-- Why choose us -->
<section class="why abs">
  <div class="why-head abs">
    <div class="eyebrow" style="display:inline-block">Why choose us</div>
    <h2 class="heading">Your Partner in Tree<br>Presevation</h2>
  </div>
  <div class="feature abs" style="left:121px;top:218px">
    <svg width="32" height="32" viewBox="0 0 32 32" fill="none" stroke="var(--green)" stroke-width="1.6"><path d="M4 28h24M8 28l4-10h8l4 10M16 4v14M11 9l5-5 5 5"/></svg>
    <div><h3>Proven Record</h3><p>Inventore veritasis uas<br>vitae dicta sunt</p></div>
  </div>
  <div class="feature abs" style="left:367px;top:218px">
    <svg width="32" height="32" viewBox="0 0 32 32" fill="none" stroke="var(--green)" stroke-width="1.6"><path d="M16 3l4 5 6 1-1 6 3 5-5 3-1 6-6-2-6 2-1-6-5-3 3-5-1-6 6-1z"/></svg>
    <div><h3>Prfessionalism</h3><p>Inventore veritasis uas<br>vitae dicta sunt</p></div>
  </div>
  <div class="feature abs" style="left:121px;top:343px">
    <svg width="32" height="32" viewBox="0 0 32 32" fill="none" stroke="var(--green)" stroke-width="1.6"><circle cx="16" cy="16" r="12"/><path d="M16 4v6M16 16l6-4M10 26l2-4h8l2 4"/></svg>
    <div><h3>Expertise</h3><p>Inventore veritasis uas<br>vitae dicta sunt</p></div>
  </div>
  <div class="feature abs" style="left:367px;top:343px">
    <svg width="32" height="32" viewBox="0 0 32 32" fill="none" stroke="var(--green)" stroke-width="1.6"><circle cx="13" cy="9" r="5"/><path d="M4 28c0-6 4-10 9-10s9 4 9 10M22 14l3 3 5-6"/></svg>
    <div><h3>Client-Centric</h3><p>Inventore veritasis uas<br>vitae dicta sunt</p></div>
  </div>
</section>
<div class="worker abs" role="img" aria-label="Photo of a tree care worker in a hard hat and safety vest with arms crossed"></div>

<!-- Services -->
<section class="services abs" role="img" aria-label="Dark photo of tree bark behind the services section">
  <div class="services-head abs">
    <div class="eyebrow">Our services</div>
    <h2 class="heading">Services We Provide</h2>
  </div>
  <div class="svc abs" style="left:119px;top:199px">
    <div class="svc-img" style="background:linear-gradient(160deg,#6f9a4a,#3f5f2c 60%,#8aa36e)" role="img" aria-label="Photo of a worker pruning a branch with long-handled shears"></div>
    <div class="svc-card"><span>Tree Pruning</span><b>Duis aute irure dolor inea...</b></div>
  </div>
  <div class="svc abs" style="left:448px;top:199px">
    <div class="svc-img" style="background:linear-gradient(180deg,#8ac24f,#76ad3c)" role="img" aria-label="Green-tinted photo of a tree removal job"></div>
    <div class="svc-icon"><svg width="22" height="22" viewBox="0 0 24 24" fill="none" stroke="#fff" stroke-width="2"><path d="M14 4h6v6M20 4l-9 9M18 14v6H4V6h6"/></svg></div>
    <div class="svc-card"><span>Tree Removal</span><b>Duis aute irure dolor inea...</b></div>
  </div>
  <div class="svc abs" style="left:774px;top:199px">
    <div class="svc-img" style="background:linear-gradient(160deg,#4b6e38,#2f4a25 55%,#8fb267)" role="img" aria-label="Photo of two workers inspecting a row of hedges"></div>
    <div class="svc-card"><span>Stump Grinding</span><b>Duis aute irure dolor inea...</b></div>
  </div>
</section>

<!-- Testimonials -->
<div class="avatar abs" style="left:325px;top:2621px;width:84px;height:84px;background:linear-gradient(160deg,#d9d6d2,#8e8a86)" role="img" aria-label="Portrait of a client"></div>
<div class="avatar abs" style="left:148px;top:2671px;width:104px;height:104px;background:linear-gradient(160deg,#7ba1b7,#3a4450)" role="img" aria-label="Portrait of a client"></div>
<div class="avatar abs" style="left:276px;top:2729px;width:148px;height:148px;background:linear-gradient(160deg,#c9b6a0,#e9e2d8)" role="img" aria-label="Portrait of a client"></div>
<div class="avatar abs" style="left:146px;top:2833px;width:126px;height:126px;background:linear-gradient(160deg,#4b5258,#2a3036)" role="img" aria-label="Portrait of a client"></div>
<div class="avatar abs" style="left:318px;top:2896px;width:110px;height:110px;background:linear-gradient(160deg,#b7cbe0,#2b3142)" role="img" aria-label="Portrait of a client"></div>
<div class="timeline abs"></div>
<div class="dot abs" style="left:540px;top:2726px"></div>
<div class="dot abs" style="left:540px;top:2780px"></div>
<div class="dot abs" style="left:540px;top:2833px"></div>
<div class="dot on abs" style="left:540px;top:2887px"></div>
<div class="quote abs">
  <h2>People Love Us</h2>
  <div class="stars">★★★★★</div>
  <p>Lorem ipsum dolor sit amet, consectetur adipiscing elit, sed do eiusmod tempor incididunt ut labore et dolore magna aliqua. tempor incididunt ut labore et dolore magna aliqua</p>
  <div class="author">
    <div class="avatar" style="background:linear-gradient(160deg,#b7cbe0,#2b3142)" role="img" aria-label="Portrait of the reviewer"></div>
    <div><b>Clara Whitmore</b><span>Senior Director</span></div>
  </div>
</div>

<!-- Contact -->
<section class="contact abs" role="img" aria-label="Soft photo of a green meadow with trees"></section>
<div class="touch abs">
  <h2>GET IN <b>TOUCH</b></h2>
  <p>Lorem ipsum dolor sit amet, consectetur adipiscing elit, sed do eiu smod tempor incididunt ut labore et dolore magna aliqua.</p>
  <div class="info" style="margin-left:-4px">
    <div class="ic"><svg width="18" height="20" viewBox="0 0 24 28"><path d="M12 26s9-9 9-15a9 9 0 0 0-18 0c0 6 9 15 9 15z" fill="#fff"/><circle cx="12" cy="11" r="3" fill="var(--green)"/></svg></div>
    <div><h4>OAKRIDGE OFFICE</h4><span>402 Cedar Hollow Road,<br>Suite 12, Oakridge, OR 97001</span></div>
  </div>
  <div class="info" style="margin-left:-4px;margin-top:26px">
    <div class="ic"><svg width="18" height="18" viewBox="0 0 24 24"><path d="M6.6 10.8a15 15 0 0 0 6.6 6.6l2.2-2.2a1 1 0 0 1 1-.25 11.4 11.4 0 0 0 3.6.57 1 1 0 0 1 1 1V20a1 1 0 0 1-1 1A17 17 0 0 1 3 4a1 1 0 0 1 1-1h3.5a1 1 0 0 1 1 1c0 1.25.2 2.45.57 3.6a1 1 0 0 1-.25 1z" fill="#fff"/></svg></div>
    <div><h4>PHONE NUMBER</h4><span>+555 310- 2284</span></div>
  </div>
  <div class="socials"><i aria-label="Social link"></i><i aria-label="Social link"></i><i aria-label="Social link"></i></div>
</div>
<form class="form abs">
  <h3>LEAVE US A MESSAGE</h3>
  <div class="field first">Email address</div>
  <div class="field">Subject</div>
  <div class="field tall">Write Your Message Here</div>
  <div class="btn">SEND MESSAGE</div>
</form>

<!-- Footer -->
<footer class="footer abs">
  <svg width="1200" height="397" class="abs" style="left:0;top:0">
    <path d="M0 62Q300 -6 600 -6Q900 -6 1200 62V397H0Z" fill="var(--footer)" transform="translate(0,42)"/>
    <path d="M235 20Q600 -30 965 20" fill="none" stroke="var(--green)" stroke-width="4"/>
  </svg>
</footer>
<div class="badge abs" style="left:575px;top:3608px"><i></i></div>
<div class="foot-brand abs">
  <div class="brand">
    <div class="brand-mark" style="background:var(--white);width:56px;height:56px"></div>
    <div class="brand-name">VERDELL<br>TREE CARE</div>
  </div>
  <p>There are many variations of passages of Lorem Ipsum available, but the ma-jority have suffered alteration</p>
</div>
<div class="foot-social abs"><i></i><i></i><i></i><i></i></div>
<div class="foot-col abs" style="left:488px;top:3802px">
  <h4>Company</h4>
  <ul style="margin-top:18px;margin-left:2px"><li>Services</li><li>Services</li><li>Services</li><li>Services</li></ul>
</div>
<div class="foot-col abs" style="left:681px;top:3840px">
  <ul><li>Services</li><li>Services</li><li>Services</li><li>Services</li></ul>
</div>
<div class="foot-col news abs" style="left:878px;top:3802px">
  <h4 style="margin-left:6px">Subscribe Newsletter</h4>
  <div class="news-field">Enter your email...</div>
  <div class="news-btn">SUBMIT</div>
</div>

</body>
</html>
```